Brightway Carpet and Tile cleaning Business card Design

I need a design that has the same feel as my van.
i would also like a prominent "Review us on facebook" somewhere, but not that it makes it look silly.
I would like the card to have a little bit of grey or black in the design as well.

It will need contact details
phone: 0455 817264
email: rkbrightwayclean@mailbox-example.com
website: www.brightwaycarpetandtilecleaning-example.com.au
facebook: /brightwaycarpetandtilecleaning

Industry/Entity Type

Business

Contact Information for Business Card

Phone number 0455817264
Email rkbrightwayclean@mailbox-example.com
Website www.brightwaycarpetandtilecleaning-example.com.au
Facebook/brightwaycarpetandtilecleaning

Colors
000000

Requirements
Must have
• Same feel as my van
• I want the card to stand out from the crowd
Nice to have
• Maybe include a tiny bit of a third colour? Grey's,blacks, orange?

```html
<!DOCTYPE html>
<html lang="en">
<head>
<meta charset="utf-8">
<title>Brightway Carpet and Tile Cleaning – Business Card</title>
<link rel="stylesheet" href="https://fonts.googleapis.com/css2?family=Michroma&family=Open+Sans:wght@400;600;700&display=swap">
<style>
  :root {
    --backdrop: #3b3b3b;
    --card-white: #ffffff;
    --aqua: #1bb0e0;
    --aqua-deep: #0f9fd3;
    --aqua-light: #bfe8f7;
    --lime: #8cc63f;
    --charcoal: #141414;
    --charcoal-soft: #262626;
    --ink-white: #ffffff;
    --ink-grey: #d9d9d9;
  }
  * { box-sizing: border-box; margin: 0; padding: 0; }
  html, body { width: 1105px; height: 1200px; overflow: hidden; }
  body {
    background: var(--backdrop);
    font-family: "Open Sans", Arial, sans-serif;
    position: relative;
  }
  .card {
    position: absolute;
    left: 196px;
    width: 720px;
    height: 411px;
    overflow: hidden;
    box-shadow: 0 4px 14px rgba(0,0,0,.45);
  }
  .card--front { top: 146px; background: var(--card-white); }
  .card--back {
    top: 602px;
    background: linear-gradient(115deg, var(--charcoal) 0%, var(--charcoal-soft) 55%, #3a3a3a 64%, var(--charcoal) 80%);
  }
  .card__art { position: absolute; inset: 0; width: 100%; height: 100%; }

  .bubble-area {
    position: absolute;
    left: 400px; top: 10px;
    width: 310px; height: 250px;
    background: radial-gradient(ellipse at 60% 45%, var(--aqua-light) 0%, rgba(191,232,247,.45) 45%, rgba(255,255,255,0) 72%);
  }

  .brand-name {
    position: absolute;
    font-family: "Michroma", Arial, sans-serif;
    color: var(--aqua);
    white-space: nowrap;
    display: flex;
    align-items: center;
    gap: 12px;
  }
  .brand-name__dot {
    width: 18px; height: 18px; border-radius: 50%;
    background: var(--lime);
    flex: none;
  }
  .card--front .brand-name { left: 50px; top: 62px; font-size: 30px; }
  .card--back .brand-name { left: 0; right: 0; justify-content: center; top: 165px; font-size: 36px; }

  .contact-list {
    position: absolute; left: 34px; top: 303px;
    list-style: none;
    color: var(--ink-white);
    font-size: 17px;
    line-height: 27px;
  }
  .contact-list li { display: flex; align-items: center; gap: 12px; }
  .contact-list svg { width: 17px; height: 17px; flex: none; }
  .contact-list .icon-square { width: 15px; height: 15px; background: var(--ink-white); flex: none; margin: 0 1px; }

  .owner {
    position: absolute; right: 38px; top: 328px;
    text-align: right; color: var(--ink-white);
  }
  .owner__name { font-family: "Michroma", Arial, sans-serif; font-size: 22px; line-height: 30px; }
  .owner__role { font-weight: 600; font-size: 19px; line-height: 28px; letter-spacing: .5px; }

  .website {
    position: absolute; left: 0; right: 0; top: 290px;
    text-align: center; color: var(--ink-grey);
    font-size: 17px; letter-spacing: .6px; text-transform: uppercase;
  }
  .review {
    position: absolute; left: 0; right: 0; top: 336px;
    display: flex; justify-content: center; align-items: center; gap: 16px;
    color: var(--aqua); font-weight: 700; font-size: 28px;
  }
  .review__square { width: 28px; height: 28px; background: var(--lime); }
</style>
</head>
<body>

<section class="card card--front" aria-label="Business card front">
  <div class="bubble-area" role="img" aria-label="Decorative cluster of soap bubbles"></div>
  <svg class="card__art" viewBox="0 0 720 411" preserveAspectRatio="none" aria-hidden="true">
    <defs>
      <linearGradient id="sea" x1="0" y1="0" x2="0" y2="1">
        <stop offset="0" stop-color="#22bde8"/>
        <stop offset="1" stop-color="#0fa3d6"/>
      </linearGradient>
    </defs>
    <path d="M0,218 C150,178 270,330 430,300 C560,278 640,208 720,212 L720,411 L0,411 Z" fill="var(--lime)"/>
    <path d="M0,246 C150,212 270,352 430,326 C560,306 640,236 720,240 L720,411 L0,411 Z" fill="url(#sea)"/>
  </svg>

  <div class="brand-name"><span class="brand-name__dot"></span>Brightway Clean</div>

  <ul class="contact-list">
    <li>
      <svg viewBox="0 0 24 24" aria-hidden="true"><path fill="#fff" d="M6.6 10.8a15.1 15.1 0 0 0 6.6 6.6l2.2-2.2c.3-.3.7-.4 1-.2 1.1.4 2.3.6 3.6.6.6 0 1 .4 1 1V20c0 .6-.4 1-1 1C10.6 21 3 13.4 3 4c0-.6.4-1 1-1h3.5c.6 0 1 .4 1 1 0 1.3.2 2.5.6 3.6.1.3 0 .7-.2 1z"/></svg>
      0455817264
    </li>
    <li>
      <svg viewBox="0 0 24 24" aria-hidden="true"><rect x="2" y="5" width="20" height="14" fill="none" stroke="#fff" stroke-width="2"/><path d="M2 5l10 8 10-8" fill="none" stroke="#fff" stroke-width="2"/></svg>
      rkbrightwayclean@mailbox-example.com
    </li>
    <li><span class="icon-square" aria-hidden="true"></span>brightwaycarpetandtilecleaning</li>
  </ul>

  <div class="owner">
    <p class="owner__name">RYAN KESSLER</p>
    <p class="owner__role">OWNER/OPERATOR</p>
  </div>
</section>

<section class="card card--back" aria-label="Business card back">
  <div class="card__art" role="img" aria-label="Soft dark background with faint bubbles and a glossy diagonal sheen"></div>
  <div class="brand-name"><span class="brand-name__dot"></span>Brightway Clean</div>
  <p class="website">www.brightwaycarpetandtilecleaning-example.com.au</p>
  <p class="review">REVIEW US ON <span class="review__square" aria-hidden="true"></span></p>
</section>

</body>
</html>
```